KAJU Freightways #ALLKAJU Business Cards & Letterhead

I am looking to business cards designed for our organization. We are currently undergoing a small re-branding that is taking place. Our organization is called KAJU Freightways and we are headquartered in Phoenix, AZ. We primarily provide transportation and logistics services to the Marlow Parcel Bureau who is our largest customer. I would like to see a design that incorporates name, title, contact info, website, and address (this will be different depending on the employee). I would also like to see some color on the business card using our logo colors or a variation. I would like our logo on the back of the business card with the website displayed. The final design should communicate that we are a next generation transportation operate that focuses on being driver-first, customer-centric, innovative, and sustainable.We would also like our #ALLKAJU catch phrase incorporated as well.

Target Market(s)

Transportation & Logistics

Industry/Entity Type

Trucking Company

Contact Information for Business Card

-First and Last Name
-Position Title
-Contact Phone
-Contact Email
-Physical Address

Font styles to use
Serif

Colors

Designer to choose colors to be used in the design.

Requirements
Must have
• -KAJU logo prominently displayed
• -#ALLKAJU catch phrase used
• -Some amount of color, design gradient, etc.
• -Logo on the back with website listed (https://www.kajufreightco.example)

```html
<!DOCTYPE html>
<html lang="en">
<head>
<meta charset="utf-8">
<title>KAJU Freightways Business Card</title>
<link href="https://fonts.googleapis.com/css2?family=Roboto:wght@400;700&display=swap" rel="stylesheet">
<style>
  :root {
    --backdrop: #6b6b6b;
    --card-dark: #202020;
    --card-light: #ffffff;
    --teal: #0d5666;
    --ink: #0f3942;
    --green: #8cc63f;
    --silver: #b9b9b9;
    --text-grey: #3a3a3a;
  }
  * { margin: 0; padding: 0; box-sizing: border-box; }
  html, body { width: 1200px; height: 960px; overflow: hidden; }
  body {
    background: var(--backdrop);
    font-family: "Roboto", Arial, sans-serif;
    position: relative;
  }
  .card {
    position: absolute;
    left: 250px;
    width: 700px;
    height: 400px;
    border-radius: 24px;
    overflow: hidden;
  }
  .card-back { top: 50px; background: var(--card-dark); }
  .card-front { top: 510px; background: var(--card-light); }

  .back-mark {
    position: absolute;
    left: 50%; top: 40px;
    width: 210px; height: 210px;
    transform: translateX(-50%);
    border: 3px solid var(--silver);
    border-radius: 50%;
    display: flex; align-items: center; justify-content: center;
  }
  .back-mark .wordmark {
    font-weight: 700;
    font-size: 58px;
    color: var(--silver);
    letter-spacing: 1px;
  }
  .back-footer {
    position: absolute;
    left: 0; right: 0; top: 286px;
    text-align: center;
    color: var(--silver);
  }
  .back-footer .tagline {
    font-weight: 700;
    font-size: 20px;
    letter-spacing: 2px;
    color: var(--green);
  }
  .back-footer .website {
    font-size: 15px;
    margin-top: 8px;
    letter-spacing: 0.5px;
  }

  .front-shapes { position: absolute; inset: 0; }
  .front-wordmark {
    position: absolute;
    left: 52px; top: 96px;
    font-weight: 700;
    font-size: 112px;
    line-height: 1;
    color: var(--ink);
    letter-spacing: 2px;
  }
  .contact {
    position: absolute;
    left: 52px; top: 262px;
    color: var(--text-grey);
    font-size: 15px;
    line-height: 1.3;
  }
  .contact .address { margin-bottom: 10px; }
  .contact-line { display: flex; align-items: center; gap: 10px; }
  .contact-line svg { width: 13px; height: 13px; fill: var(--ink); flex: none; }
  .person {
    position: absolute;
    right: 36px; bottom: 60px;
    text-align: right;
  }
  .person .name {
    color: var(--green);
    font-weight: 700;
    font-size: 19px;
    letter-spacing: 0.5px;
  }
  .person .title {
    color: #ffffff;
    font-size: 14px;
    margin-top: 2px;
  }
</style>
</head>
<body>
  <section class="card card-back">
    <div class="back-mark"><span class="wordmark">KAJU</span></div>
    <div class="back-footer">
      <div class="tagline">#ALLKAJU</div>
      <div class="website">https://www.kajufreightco.example</div>
    </div>
  </section>

  <section class="card card-front">
    <svg class="front-shapes" viewBox="0 0 700 400" width="700" height="400">
      <path d="M470,0 C575,120 575,285 445,400 L700,400 L700,0 Z" fill="var(--teal)"/>
      <path d="M438,0 C548,125 545,290 415,400 L398,400 C512,292 518,132 428,0 Z" fill="var(--green)"/>
    </svg>

    <div class="front-wordmark">KAJU</div>

    <div class="contact">
      <div class="address">214 Cactus Ridge Road<br>Phoenix, Arizona 85004</div>
      <div class="contact-line">
        <svg viewBox="0 0 24 24"><path d="M6.6 10.8a15 15 0 0 0 6.6 6.6l2.2-2.2c.3-.3.7-.4 1-.2 1.1.4 2.3.6 3.6.6.6 0 1 .4 1 1V20c0 .6-.4 1-1 1A17 17 0 0 1 3 4c0-.6.4-1 1-1h3.5c.6 0 1 .4 1 1 0 1.3.2 2.5.6 3.6.1.3 0 .7-.2 1z"/></svg>
        <span>602-555-0148</span>
      </div>
      <div class="contact-line">
        <svg viewBox="0 0 24 24"><path d="M2 5h20v14H2z M2 5l10 8 10-8" /></svg>
        <span>dreyes@kajufreightco.example</span>
      </div>
      <div class="contact-line">
        <svg viewBox="0 0 24 24"><circle cx="12" cy="12" r="10"/></svg>
        <span>www.kajufreightco.example</span>
      </div>
    </div>

    <div class="person">
      <div class="name">DANIEL REYES</div>
      <div class="title">President</div>
    </div>
  </section>
</body>
</html>
```